Brand new letterhead, business card, email signature etc.

We are a financial company in London, UK. Our website is www.marlowvane.com. We're wanting a complete remodel of the company colours, letter head, business cards, email signatures, etc. Looking to keep the same font for the company name. I have upload a colour palette that we want to work with. We're looking for company letterhead for outgoing letters/ correspondence, letterhead for internal documentation, email signatures, e-letters. etc. Ultimately we will redesign the entire website also. It is important that our clients get a strong, secure, warm, trustworthy, solid feeling and first impression.
Updates

Designs look the same

Target Market(s)

Institutional investors, (ultra) high net worth individuals

Industry/Entity Type

Finance, Invesments banking.

Font styles to use
Other font styles liked:
• Current font is "Champagne & Limousines"

Requirements
Must have
• Must use the colours provided on the PDF uploaded to the portal. The purple = main colour. The red = accent colour.
Nice to have
• Nice to use same font as now for the company name "Corvane". Font is "Champagne & Limousines". Nice to have some reference to the old logo flower, but only subtle.
Should not have
• Do not use the colour red from our website. Use the colours provided on the colour palette PDF that I uploaded in the portal.

```html
<!DOCTYPE html>
<html lang="en">
<head>
<meta charset="utf-8">
<title>Corvane — Business Card</title>
<link rel="stylesheet" href="https://fonts.googleapis.com/css2?family=Josefin+Sans:wght@300&family=Montserrat:wght@400;700&display=swap">
<style>
  :root {
    --page: #2a2a2d;
    --main-purple: #4b2a63;
    --purple-deep: #1f1628;
    --purple-line: #6e4a8a;
    --accent-red: #c8323c;
    --cream: #f4e6d8;
    --white: #ffffff;
    --muted: #33263f;
  }
  * { margin: 0; padding: 0; box-sizing: border-box; }
  html, body {
    width: 1200px; height: 780px; overflow: hidden;
    background: var(--page);
  }
  .stage {
    position: relative; width: 1200px; height: 780px;
    display: flex; align-items: center; justify-content: center; gap: 40px;
  }
  .card {
    position: relative; width: 540px; height: 310px; overflow: hidden;
    box-shadow: 0 14px 30px rgba(0,0,0,.45);
  }

  /* Front */
  .card-front { background: var(--main-purple); }
  .brand {
    position: absolute; left: 0; right: 0; top: 50%;
    transform: translateY(-50%);
    display: flex; align-items: center; justify-content: center; gap: 26px;
  }
  .brand-square {
    width: 72px; height: 72px;
    border: 2px solid var(--purple-line);
  }
  .brand-name {
    font-family: "Josefin Sans", sans-serif; font-weight: 300;
    font-size: 50px; letter-spacing: 10px; color: var(--cream);
    line-height: 1;
  }

  /* Back */
  .card-back { background: var(--purple-deep); }
  .back-mark {
    position: absolute; left: 18px; bottom: 20px;
    display: flex; flex-direction: column; align-items: center; gap: 16px;
  }
  .back-name {
    writing-mode: vertical-rl; transform: rotate(180deg);
    font-family: "Josefin Sans", sans-serif; font-weight: 300;
    font-size: 34px; letter-spacing: 7px; line-height: 1; color: var(--muted);
  }
  .back-square {
    width: 54px; height: 54px; border: 2px solid var(--muted);
  }
  .tab {
    position: absolute; right: 0; top: 56px;
    width: 22px; height: 36px; background: var(--accent-red);
  }
  .bottom-rule {
    position: absolute; left: 0; right: 0; bottom: 0;
    height: 5px; background: var(--accent-red);
  }
  .contact {
    position: absolute; right: 34px; top: 58px;
    text-align: right; color: var(--white);
    font-family: "Montserrat", sans-serif;
  }
  .person {
    font-weight: 700; font-size: 27px; line-height: 1; letter-spacing: .2px;
  }
  .person .first { color: var(--accent-red); }
  .role { font-size: 12px; margin-top: 6px; }
  .address { font-size: 12px; line-height: 1.5; margin-top: 14px; }
  .lines { list-style: none; margin-top: 12px; font-size: 12px; line-height: 1.7; }
  .lines li { display: flex; align-items: center; justify-content: flex-end; gap: 8px; }
  .lines svg { width: 12px; height: 12px; flex: none; }
</style>
</head>
<body>
<main class="stage">
  <section class="card card-front" aria-label="Card front">
    <div class="brand">
      <span class="brand-square"></span>
      <span class="brand-name">CORVANE</span>
    </div>
  </section>

  <section class="card card-back" aria-label="Card back">
    <div class="back-mark" aria-hidden="true">
      <span class="back-name">CORVANE</span>
      <span class="back-square"></span>
    </div>
    <span class="tab"></span>
    <div class="contact">
      <p class="person"><span class="first">Lena</span> Daskova</p>
      <p class="role">Managing Director</p>
      <p class="address">418 Harlow Rd. Suite 310<br>Kingsbury, TX 75920</p>
      <ul class="lines">
        <li>(555) 214-6037
          <svg viewBox="0 0 12 12"><path fill="var(--accent-red)" d="M2.5 1l2 2.2-1 1.2a6 6 0 0 0 3.1 3.1l1.2-1 2.2 2-1.2 1.5C5 10 2 7 1 2.7z"/></svg>
        </li>
        <li>info@marlowvane.com
          <svg viewBox="0 0 12 12"><rect x="1" y="2.5" width="10" height="7" fill="var(--accent-red)"/><path d="M1.5 3l4.5 3.5L10.5 3" fill="none" stroke="var(--purple-deep)" stroke-width="1"/></svg>
        </li>
        <li>www.marlowvane.com
          <svg viewBox="0 0 12 12"><circle cx="6" cy="6" r="5" fill="var(--accent-red)"/><path d="M1 6h10M6 1c-2.5 2.8-2.5 7.2 0 10M6 1c2.5 2.8 2.5 7.2 0 10" fill="none" stroke="var(--purple-deep)" stroke-width=".8"/></svg>
        </li>
      </ul>
    </div>
    <span class="bottom-rule"></span>
  </section>
</main>
</body>
</html>
```